Hello my name is Colin, I am Starting a business called Lumen Wellness and fitness and am in need of a memorable business card.
It is a personal training studio. I have added the logo that i would like to be on the left center om my business card. i would like room left up the top for a heading sentence such as. "Is your body shocking for all the wrong reasons". there must be room left on the right of the logo below the main heading for 3 sub headings.
then under those 3 headings and logo room for another larger heading eg. "give me a call and learn how to eat chocolate, drink bear and have great sex". in what room is left i would like to be used for my contact details, use I'm Colin Ferrante your fitness expert on the left then on the right Phone, Email and website space in at least 12 Point. Very specific i know :) now onto the back, for the back i would like an eye catching graphic and room for one main headline and 3 bullet points centered just write anything i will choose what to put in them when i pick a winner. Thank you very much for sticking through all of that :) i appreciate you taking the time to read it and hopefully undergo designing me a business card.
I can't wait to see the designs!

Target Market(s)

slightly more towards females although it would probably be best if it was targeted towards both sexes

Industry/Entity Type

Training

Requirements
Nice to have
• I would love to see if anyone could come up with a design that would really make my card stand out and be memorable.
Should not have
• tacky fitness photos of abs and muscles etc.

```html
<!DOCTYPE html>
<html lang="en">
<head>
<meta charset="utf-8">
<title>Lumen Wellness and fitness – Business Card</title>
<link rel="stylesheet" href="https://fonts.googleapis.com/css2?family=Questrial&family=Open+Sans:wght@400&display=swap">
<style>
  :root {
    --backdrop: #ebe8e4;
    --card: #ffffff;
    --brand-blue: #1c4f8a;
    --brand-blue-deep: #143a68;
    --ink: #333333;
    --ink-soft: #444444;
    --band-dark: #2e2e2e;
    --label: #1a1a1a;
  }
  * { box-sizing: border-box; margin: 0; padding: 0; }
  html, body { width: 1200px; height: 788px; overflow: hidden; }
  body {
    position: relative;
    background: var(--backdrop);
    font-family: "Questrial", "Century Gothic", sans-serif;
    color: var(--ink);
  }
  .side-label {
    position: absolute;
    font-size: 21px;
    color: var(--label);
    transform: translateX(-50%);
    white-space: nowrap;
  }
  .card {
    position: absolute;
    width: 525px;
    height: 300px;
    background: var(--card);
    border-radius: 20px;
    overflow: hidden;
    box-shadow: 0 6px 14px rgba(0,0,0,0.28);
  }
  .card--front { left: 338px; top: 73px; }
  .card--back-one { left: 54px; top: 445px; }
  .card--back-two { left: 621px; top: 441px; }

  .centered { position: absolute; left: 0; right: 0; text-align: center; white-space: nowrap; }

  .tagline { font-size: 13px; color: var(--ink-soft); }
  .wordmark { color: var(--brand-blue); font-weight: 400; line-height: 1; }
  .wordmark__name { display: block; }
  .wordmark__sub { display: block; }

  .card--front .tagline { top: 21px; }
  .card--front .wordmark { top: 70px; }
  .card--front .wordmark__name { font-size: 72px; letter-spacing: 1px; }
  .card--front .wordmark__sub { font-size: 18px; margin-top: 2px; }
  .pitch { top: 183px; font-size: 13px; color: var(--brand-blue); }
  .owner { top: 210px; font-size: 14.5px; color: var(--brand-blue-deep); }
  .phone { top: 240px; font-size: 14px; color: var(--ink); }
  .field-key { font-weight: 700; font-style: italic; margin-right: 6px; font-family: "Open Sans", sans-serif; }

  .contact-band { position: absolute; left: 0; bottom: 0; width: 525px; height: 33px; }
  .contact-band__text {
    position: absolute; bottom: 8px; font-size: 13.5px; color: #ffffff; white-space: nowrap;
  }
  .contact-band__text--email { left: 40px; }
  .contact-band__text--web { left: 313px; }

  .figure-area {
    position: absolute; left: 40px; top: 20px; width: 150px; height: 265px;
    background: linear-gradient(180deg, #2a5c98 0%, #164072 100%);
    border-radius: 60px 60px 12px 12px;
  }
  .card--back-one .wordmark { position: absolute; left: 255px; top: 24px; }
  .card--back-one .wordmark__name { font-size: 36px; }
  .card--back-one .wordmark__sub { font-size: 10px; margin-top: 1px; }
  .points {
    position: absolute; left: 258px; top: 118px; list-style: none;
    font-family: "Open Sans", sans-serif; font-size: 16px; color: #111;
  }
  .points li { position: relative; padding-left: 25px; height: 34px; }
  .points li:nth-child(3) { margin-top: 2px; }
  .points li::before {
    content: ""; position: absolute; left: 0; top: 9px; width: 6px; height: 6px; background: #111;
  }
  .card--back-one .site { position: absolute; left: 256px; top: 254px; font-size: 21px; color: var(--ink-soft); }

  .card--back-two .tagline { top: 20px; }
  .card--back-two .wordmark { top: 86px; }
  .card--back-two .wordmark__name { font-size: 86px; letter-spacing: 1px; }
  .card--back-two .wordmark__sub { font-size: 22px; margin-top: 2px; }
  .card--back-two .site { top: 251px; font-size: 21px; letter-spacing: 4px; color: var(--ink-soft); }
</style>
</head>
<body>

  <div class="side-label" style="left:600px; top:33px;">Front</div>
  <div class="side-label" style="left:323px; top:404px;">Back - 1</div>
  <div class="side-label" style="left:897px; top:404px;">Back - 2</div>

  <section class="card card--front" aria-label="Card front">
    <p class="centered tagline">Is your body shocking for all the wrong reasons</p>
    <h1 class="centered wordmark">
      <span class="wordmark__name">Lumen</span>
      <span class="wordmark__sub">Wellness and fitness</span>
    </h1>
    <p class="centered pitch">give me a call and learn how to eat chocolate drink bear and have great sex</p>
    <p class="centered owner">Colin Ferrante, Fitness Expert</p>
    <p class="centered phone"><span class="field-key">p</span>: +12 555 01984</p>
    <svg class="contact-band" viewBox="0 0 525 33" aria-hidden="true">
      <defs>
        <linearGradient id="bandBlue" x1="0" x2="1" y1="0" y2="0">
          <stop offset="0" stop-color="#1c4f8a"/>
          <stop offset="1" stop-color="#123a66"/>
        </linearGradient>
      </defs>
      <polygon points="0,0 232,0 250,33 0,33" fill="url(#bandBlue)"/>
      <polygon points="240,0 525,0 525,33 258,33" fill="var(--band-dark)"/>
    </svg>
    <span class="contact-band__text contact-band__text--email"><span class="field-key">e</span>: hello@lumenstudio.example</span>
    <span class="contact-band__text contact-band__text--web"><span class="field-key">w</span>: www.lumenstudio.example</span>
  </section>

  <section class="card card--back-one" aria-label="Card back, option one">
    <div class="figure-area" role="img" aria-label="Blue silhouette illustration of a man in a suit beside a tall woman"></div>
    <div class="wordmark">
      <span class="wordmark__name">Lumen</span>
      <span class="wordmark__sub">Wellness and fitness</span>
    </div>
    <ul class="points">
      <li>Lorem Ipsum has been ...</li>
      <li>Lorem Ipsum has been ...</li>
      <li>Lorem Ipsum has been ...</li>
    </ul>
    <p class="site">www.lumenstudio.example</p>
  </section>

  <section class="card card--back-two" aria-label="Card back, option two">
    <p class="centered tagline">Is your body shocking for all the wrong reasons</p>
    <div class="centered wordmark">
      <span class="wordmark__name">Lumen</span>
      <span class="wordmark__sub">Wellness and fitness</span>
    </div>
    <p class="centered site">www.lumenstudio.example</p>
  </section>

</body>
</html>
```